Beautiful design for wordpress

I need a beautiful, colourful and feminine website. My business is called 'The Velvet Lantern', and I sell crystals, books, CD's, pendulums and other metaphysical items. I also provide Reiki (energy healing).
I want this design to be eye catching and inspire happiness and joy in those who see it. And I would love to see the use of the logo and its colours :)
Please add these on the web design: Home, About, Online store, Blog

Industry/Entity Type

Business

Requirements
Must have
• Colourful and playful, must use the logo somewhere, have the words on a menu saying 'Home, Blog, Online store and about' (or similar to those)And the design must stand out!
Should not have
• grey, brown and other boring colours.

```html
<!DOCTYPE html>
<html lang="en">
<head>
<meta charset="utf-8">
<title>The Velvet Lantern — Crystals &amp; Gifts</title>
<link rel="stylesheet" href="https://fonts.googleapis.com/css2?family=Questrial&display=swap">
<style>
:root{
  --magenta:#c43f9f;
  --pink:#e8339b;
  --orange:#fda500;
  --cream:#f9e0b0;
  --ink:#555;
  --ink-dark:#3f3f3f;
  --header-top:#f6f6f6;
  --header-bottom:#dedede;
  --white:#fff;
  --frame:#dcdcdc;
}
*{margin:0;padding:0;box-sizing:border-box}
html,body{width:843px;height:1200px;overflow:hidden;background:var(--white)}
body{position:relative;font-family:'Questrial',sans-serif;color:var(--ink)}
.abs{position:absolute}

.top-band{left:0;top:0;width:843px;height:16px;background:var(--magenta)}
.header{left:0;top:16px;width:843px;height:413px;background:linear-gradient(var(--header-top) 0%,var(--header-top) 45%,var(--header-bottom) 100%);border-bottom:1px solid #d0d0d0}

.brand{left:96px;top:44px;display:flex;align-items:center;gap:8px}
.brand-dot{width:12px;height:12px;border-radius:50%;background:var(--pink);flex:none}
.brand-name{font-size:17px;line-height:20px;color:var(--ink-dark)}

.phone{left:646px;top:35px;font-size:13px;letter-spacing:1px;color:var(--ink-dark);display:flex;align-items:center;gap:7px}
.search{left:648px;top:67px;width:103px;height:15px;border:1px solid #aaa;background:var(--white);font-size:7px;color:#888;padding:2px 3px;display:flex;justify-content:space-between;align-items:center}

.nav{left:422px;top:101px;display:flex;gap:0;font-size:12px;color:var(--ink-dark)}
.nav a{color:inherit;text-decoration:none;height:18px;line-height:18px;padding:0 9px}
.nav .current{background:var(--magenta);color:var(--white)}
.nav a+a{margin-left:11px}

.slide{top:139px;width:213px;height:262px}
.slide-1{left:93px;background:linear-gradient(135deg,#6a5a4c,#b8b0c8 50%,#5a4b3f)}
.slide-2{left:314px;background:radial-gradient(circle at 50% 50%,#d59bc0,#6ea3b8 55%,#c9c0d8)}
.slide-3{left:535px;background:linear-gradient(160deg,#c9b08a,#e8e6b0 35%,#a0663a 70%,#6e3f24)}
.arrow{top:258px}

.welcome{left:0;top:456px;width:909px;text-align:center;font-size:16px;color:var(--pink)}
.intro{left:141px;top:496px;width:628px;font-size:9.3px;line-height:16px;text-align:center;color:var(--ink)}

.section-title{font-size:16px;color:var(--pink)}
.latest{left:93px;top:580px}
.pager{left:725px;top:587px}

.product{top:617px;width:150px}
.product-frame{width:150px;height:136px;border:1px solid var(--frame);padding:4px;background:var(--white)}
.product-photo{width:100%;height:100%}
.product-name{margin-top:10px;font-size:9.4px;color:var(--pink)}
.product-text{margin-top:4px;font-size:9.4px;line-height:11px;color:var(--ink)}
.see-more{margin-top:6px;font-size:9.4px;color:var(--pink);display:flex;align-items:center;gap:4px}
.p1{left:93px}.p1 .product-photo{background:linear-gradient(135deg,#c85a5a,#e8a8c0 50%,#8a3a2a)}
.p2{left:262px}.p2 .product-photo{background:linear-gradient(135deg,#3a4a5a,#6a7a5a 50%,#c8c0a0)}
.p3{left:433px}.p3 .product-photo{background:linear-gradient(135deg,#ddd,#777 50%,#c05050)}
.p4{left:601px}.p4 .product-photo{background:linear-gradient(135deg,#a0a8b8,#3a3430 50%,#c8ccd8)}

.offer{left:93px;top:851px;width:201px;height:263px;background:var(--orange);color:var(--white)}
.offer-title{position:absolute;left:14px;top:13px;font-size:16px}
.offer-photo{position:absolute;left:14px;top:47px;width:174px;height:113px;background:linear-gradient(135deg,#f3ede6,#e8c3a8 50%,#6b4a36)}
.offer-text{position:absolute;left:14px;top:175px;width:175px;font-size:12.5px;line-height:15px}
.shop-btn{position:absolute;left:14px;top:224px;width:86px;height:23px;background:linear-gradient(#fff,#e2e2e2);border:1px solid #ccc;color:var(--ink-dark);font-size:12px;line-height:21px;text-align:center}

.blogs{left:294px;top:851px;width:457px;height:263px;background:var(--cream)}
.blogs-title{position:absolute;left:14px;top:13px;font-size:16px;color:var(--orange)}
.post{position:absolute;top:55px;width:198px}
.post-1{left:14px}.post-2{left:245px}
.post-photo{height:105px}
.post-1 .post-photo{background:linear-gradient(#d7dde8,#9aa0b8 60%,#4a3a5a)}
.post-2 .post-photo{background:radial-gradient(circle at 70% 20%,#f4f0a0,#9bb84a 45%,#3c5a20)}
.date{position:absolute;right:3px;top:64px;width:40px;height:41px;background:var(--orange);color:var(--white);text-align:center;padding-top:4px}
.date-day{font-size:15px;line-height:16px}
.date-month{font-size:8.5px;line-height:12px}
.post-title{margin-top:10px;font-size:9.3px;line-height:16px;color:var(--orange)}
.post-text{margin-top:16px;font-size:9.3px;line-height:16px;color:var(--ink)}

.footer{left:0;top:1162px;width:843px;height:38px;background:var(--magenta)}
.copyright{position:absolute;left:92px;top:14px;font-size:8px;color:var(--white)}
.social{position:absolute;left:639px;top:10px;display:flex;gap:8px}
.social span{width:22px;height:22px;border-radius:50%;border:2px solid rgba(255,255,255,.6)}
.s1{background:#3b5998}.s2{background:#f39a1d}.s3{background:#29a9e1}.s4{background:#4a4a4a}
</style>
</head>
<body>
<div class="abs top-band"></div>
<header class="abs header"></header>

<div class="abs brand">
  <span class="brand-dot"></span>
  <span class="brand-name">The Velvet<br>Lantern</span>
</div>

<div class="abs phone">
  <svg width="10" height="11" viewBox="0 0 10 11"><path d="M2 0.5 L4 2.8 L3 4.2 Q4.2 6.8 6.4 7.8 L7.6 6.8 L9.6 8.8 L8.4 10.4 Q3.6 10 0.8 3 Z" fill="#e8339b"/></svg>
  1300 482 916
</div>
<div class="abs search">Search
  <svg width="8" height="8" viewBox="0 0 8 8"><circle cx="3" cy="3" r="2.2" fill="none" stroke="#777" stroke-width="1"/><path d="M4.6 4.6 L7.5 7.5" stroke="#777" stroke-width="1.2"/></svg>
</div>

<nav class="abs nav">
  <a class="current" href="#">Home</a>
  <a href="#">About</a>
  <a href="#">Online store</a>
  <a href="#">Blog</a>
  <a href="#">Contact us</a>
</nav>

<div class="abs slide slide-1" role="img" aria-label="Lavender stone bracelet on a rose quartz crystal"></div>
<div class="abs slide slide-2" role="img" aria-label="Iridescent bismuth crystals"></div>
<div class="abs slide slide-3" role="img" aria-label="Candles with a woven basket and flowers"></div>
<svg class="abs arrow" style="left:66px" width="14" height="26" viewBox="0 0 14 26"><path d="M13 1 L1 13 L13 25" fill="none" stroke="#c43f9f" stroke-width="1.6"/></svg>
<svg class="abs arrow" style="left:763px" width="14" height="26" viewBox="0 0 14 26"><path d="M1 1 L13 13 L1 25" fill="none" stroke="#c43f9f" stroke-width="1.6"/></svg>

<h1 class="abs welcome" style="font-weight:normal">Welcome to Our Online Store</h1>
<p class="abs intro">Our caregivers understand the complexities of the aging process and are receptive to the emotional and physical needs of our clients. They provide open and affirming support as they meet client needs and are skilled in addressing life with dignity issues and options. You may inter-view and choose the provider who you feel matches your needs best or leave the placement to us.</p>

<h2 class="abs section-title latest" style="font-weight:normal">Latest Products</h2>
<svg class="abs pager" width="24" height="12" viewBox="0 0 24 12"><path d="M6 1 L1 6 L6 11 M18 1 L23 6 L18 11" fill="none" stroke="#c43f9f" stroke-width="1.3"/></svg>

<div class="abs product p1">
  <div class="product-frame"><div class="product-photo" role="img" aria-label="Rose quartz heart among tumbled stones"></div></div>
  <div class="product-name">Proin gravida nibh vel auctor</div>
  <div class="product-text">Aenean sollicitudin, lorem quis bibendum auctor, nisi elit</div>
  <div class="see-more">See More <svg width="9" height="9" viewBox="0 0 9 9"><circle cx="4.5" cy="4.5" r="4.5" fill="#555"/><path d="M3.5 2.5 L5.5 4.5 L3.5 6.5" fill="none" stroke="#fff" stroke-width="1.2"/></svg></div>
</div>
<div class="abs product p2">
  <div class="product-frame"><div class="product-photo" role="img" aria-label="Fairy figurine beside a crystal ball"></div></div>
  <div class="product-name">Proin gravida nibh vel auctor</div>
  <div class="product-text">Aenean sollicitudin, lorem quis bibendum auctor, nisi elit</div>
  <div class="see-more">See More <svg width="9" height="9" viewBox="0 0 9 9"><circle cx="4.5" cy="4.5" r="4.5" fill="#555"/><path d="M3.5 2.5 L5.5 4.5 L3.5 6.5" fill="none" stroke="#fff" stroke-width="1.2"/></svg></div>
</div>
<div class="abs product p3">
  <div class="product-frame"><div class="product-photo" role="img" aria-label="Rack of music CDs"></div></div>
  <div class="product-name">Proin gravida nibh vel auctor</div>
  <div class="product-text">Aenean sollicitudin, lorem quis bibendum auctor, nisi elit</div>
  <div class="see-more">See More <svg width="9" height="9" viewBox="0 0 9 9"><circle cx="4.5" cy="4.5" r="4.5" fill="#555"/><path d="M3.5 2.5 L5.5 4.5 L3.5 6.5" fill="none" stroke="#fff" stroke-width="1.2"/></svg></div>
</div>
<div class="abs product p4">
  <div class="product-frame"><div class="product-photo" role="img" aria-label="Shop shelves with crystals and books"></div></div>
  <div class="product-name">Proin gravida nibh vel auctor</div>
  <div class="product-text">Aenean sollicitudin, lorem quis bibendum auctor, nisi elit</div>
  <div class="see-more">See More <svg width="9" height="9" viewBox="0 0 9 9"><circle cx="4.5" cy="4.5" r="4.5" fill="#555"/><path d="M3.5 2.5 L5.5 4.5 L3.5 6.5" fill="none" stroke="#fff" stroke-width="1.2"/></svg></div>
</div>

<section class="abs offer">
  <div class="offer-title">Special Offer</div>
  <div class="offer-photo" role="img" aria-label="Relaxing spa treatment"></div>
  <div class="offer-text">Proin gravida nibh vel velit auctor aliquet. Aenean</div>
  <div class="shop-btn">Shop Now</div>
</section>

<section class="abs blogs">
  <div class="blogs-title">Recent Blogs</div>
  <article class="post post-1">
    <div class="post-photo" role="img" aria-label="Meditating figure with glowing chakras on a lotus"></div>
    <div class="date"><div class="date-day">15</div><div class="date-month">May</div></div>
    <div class="post-title">Proin gravida nibh vel velit auctor aliquet. Aenean sollicitudin</div>
    <div class="post-text">Lorem quis bibendum auctor, nisi elit cons equat ipsum, nec sagittis sem nibh id elit.</div>
  </article>
  <article class="post post-2">
    <div class="post-photo" role="img" aria-label="White water lily in sunlight"></div>
    <div class="date"><div class="date-day">14</div><div class="date-month">May</div></div>
    <div class="post-title">Proin gravida nibh vel velit auctor aliquet. Aenean sollicitudin</div>
    <div class="post-text">Lorem quis bibendum auctor, nisi elit conse-quat ipsum, nec sagittis sem nibh id elit. Duis</div>
  </article>
</section>

<footer class="abs footer">
  <div class="copyright">copyright © 2014 | Privacy Policy</div>
  <div class="social"><span class="s1"></span><span class="s2"></span><span class="s3"></span><span class="s4"></span></div>
</footer>
</body>
</html>
```